Kelvaro.ch is looking for business card letterhead and envelope C5 with WOW effect

We need a strong business card for our company Kelvaro.ch, logo is available. You want a black or dark background on which the logo Stark r% 26 # 252; appears. Letterhead and envelope in C5 format should be in a similar design, but does not have to be We need a strong business card for our company Kelvaro.ch, logo is available. A black or dark background is desired, on which the logo Stark comes across. The letterhead and the envelope in C5 format should have a similar design.

Target Market(s)

Private customers as well as entrepreneurs

Contact Information for Business Card

E-mail: info@kelvaro-example.ch
Web.www.Kelvaro-example.ch
Tel: +41 ( 0 ) 79 482 6037
Adresse:
Lindenweg 14
9406 Tarnbach

Hier kann man Icons verwenden für Email,Tel und Adressse

Font styles to use
Other font styles liked:
• Dubai,bold

Colors

Designer to choose colors to be used in the design.

Requirements
Must have
• WOW effect
Nice to have
• R% 26 # 252; back business card with our service listings. - VEHICLE LABELING - SHOP WINDOW LABELING - STICKERS AND MUCH MORE ... in red color

```html
<!DOCTYPE html>
<html lang="en">
<head>
<meta charset="utf-8">
<title>Kelvaro.ch – Business Card</title>
<link href="https://fonts.googleapis.com/css2?family=Archivo:wght@400;700;800&display=swap" rel="stylesheet">
<style>
  :root {
    --yellow: #fcc81d;
    --yellow-soft: #f2bd14;
    --black: #0b0b0b;
    --red: #e0131b;
    --white: #ffffff;
    --ink: #1a1a1a;
    --bg: #d9d9d9;
    --rule: #c9c9c9;
  }
  * { box-sizing: border-box; margin: 0; padding: 0; }
  html, body {
    width: 1200px; height: 1015px; overflow: hidden;
    background: var(--bg);
    font-family: "Archivo", Arial, sans-serif;
  }
  .card {
    position: absolute; left: 240px;
    width: 720px; height: 430px;
    overflow: hidden;
    box-shadow: 0 8px 24px rgba(0,0,0,.25);
  }
  /* Front */
  .card-front { top: 52px; background: var(--yellow); }
  .front-texture {
    position: absolute; left: 30px; top: 70px; width: 300px; height: 300px;
    background: radial-gradient(circle at 40% 45%, var(--yellow-soft) 0%, rgba(242,189,20,0) 70%);
  }
  .front-name {
    position: absolute; right: 70px; top: 150px;
    font-weight: 800; font-size: 56px; letter-spacing: 1px;
    color: var(--black); text-transform: uppercase;
  }
  .service-band {
    position: absolute; left: 0; right: 0; top: 240px; height: 86px;
    background: var(--black);
    display: flex; flex-direction: column; justify-content: center; align-items: flex-end;
    padding-right: 70px;
    color: var(--red); font-weight: 800; font-size: 17px; text-transform: uppercase;
    line-height: 1.45; letter-spacing: .3px;
  }
  .service-band .line-2 { padding-right: 80px; }
  /* Back */
  .card-back { top: 533px; background: var(--white); }
  .brand {
    position: absolute; left: 70px; top: 175px;
    display: flex; align-items: center; gap: 16px;
  }
  .brand-square { width: 34px; height: 34px; background: var(--yellow); }
  .brand-name {
    font-weight: 800; font-size: 36px; color: var(--black);
    text-transform: uppercase; letter-spacing: .5px;
  }
  .divider {
    position: absolute; left: 412px; top: 40px; width: 1px; height: 220px;
    background: linear-gradient(to bottom, rgba(201,201,201,0), var(--rule), rgba(201,201,201,0));
  }
  .contacts {
    position: absolute; left: 440px; top: 85px;
    list-style: none; font-size: 19px; color: var(--ink);
  }
  .contacts li { display: flex; align-items: center; gap: 12px; height: 36px; }
  .contacts svg { width: 22px; height: 22px; flex: none; }
  .address-band {
    position: absolute; left: 0; right: 0; bottom: 0; height: 120px;
    background: var(--yellow);
    display: flex; align-items: center; justify-content: flex-end; padding-right: 90px;
    font-size: 21px; color: var(--ink);
  }
</style>
</head>
<body>
  <section class="card card-front" aria-label="Business card front">
    <div class="front-texture" role="img" aria-label="Soft honeycomb background texture"></div>
    <h1 class="front-name">Kelvaro.ch</h1>
    <div class="service-band">
      <p class="line-1">Vehicle labeling &nbsp;|&nbsp; Shop window labeling</p>
      <p class="line-2">Stickers and much more ...</p>
    </div>
  </section>

  <section class="card card-back" aria-label="Business card back">
    <div class="brand">
      <span class="brand-square"></span>
      <span class="brand-name">Kelvaro.ch</span>
    </div>
    <div class="divider"></div>
    <ul class="contacts">
      <li>
        <svg viewBox="0 0 24 24" aria-hidden="true"><rect x="1.5" y="1.5" width="21" height="21" rx="3" fill="none" stroke="#fcc81d" stroke-width="2"/><path d="M8 6.5l2 2.5-1.3 1.5a8 8 0 0 0 4.8 4.8l1.5-1.3 2.5 2-1.3 2.2c-4.5 0-10-5.5-10-10z" fill="#fcc81d"/></svg>
        +41 ( 0 ) 79 482 6037
      </li>
      <li>
        <svg viewBox="0 0 24 24" aria-hidden="true"><rect x="1.5" y="5" width="21" height="14" fill="#fcc81d"/><path d="M1.5 5l10.5 8 10.5-8" fill="none" stroke="#fff" stroke-width="1.6"/></svg>
        info@kelvaro-example.ch
      </li>
      <li>
        <svg viewBox="0 0 24 24" aria-hidden="true"><circle cx="12" cy="12" r="10" fill="#fcc81d"/><g fill="none" stroke="#fff" stroke-width="1.3"><ellipse cx="12" cy="12" rx="4.5" ry="10"/><path d="M2 12h20M4 7h16M4 17h16"/></g></svg>
        www.Kelvaro-example.ch
      </li>
    </ul>
    <div class="address-band">Lindenweg 14, 9406 Tarnbach</div>
  </section>
</body>
</html>
```